Computer consultant business card

Bexil Software is a newly started computer consulting company. It's a small one-man company that provides mostly Vornix applications but also websites in collaboration with designers. I'm running this company on the side of full time university studies.

I want the final design to be clean and memorable. Be creative! :)

Some inspiration:
http://www.pixelmarta.com/design/48317
http://www.pixelmarta.com/design/2739164/business-card-design-by-frostlynk
http://www.pixelmarta.com/design/604281/business-card-design-by-koralind-vestrabanu

See attachment for my company logo.
Updates

I would like to thank everyone for submitting! I'll need a couple of days to review and ultimately select a design.

Target Market(s)

Non-technical entrepreneurs and small companies.

Industry/Entity Type

University

Requirements
Must have
• My company logo.
In any way, both colors from my logo.
First- and last name, e-mail and phone number.
Double-sided design.
Nice to have
• Something creative with the symbol in my logo

```html
<!DOCTYPE html>
<html lang="en">
<head>
<meta charset="utf-8">
<title>Bexil Software – Business Card</title>
<link rel="stylesheet" href="https://fonts.googleapis.com/css2?family=Josefin+Sans:wght@300;400&display=swap">
<style>
  :root {
    --stage: #1f2a2a;
    --card-back: #2b2b2e;
    --card-back-light: #4a4a4e;
    --card-front: #2a2529;
    --disc: #332e33;
    --ring-blue: #3b78c4;
    --ring-blue-deep: #2f5fa8;
    --logo-sand: #c9bfa3;
    --ink-light: #e6e6e8;
    --ink-muted: #a9a9ae;
    --ink-dim: #6f6a6f;
  }
  * { margin: 0; padding: 0; box-sizing: border-box; }
  html, body { width: 1200px; height: 1000px; overflow: hidden; background: var(--stage); }
  .canvas { position: relative; width: 1200px; height: 1000px; font-family: "Josefin Sans", sans-serif; }

  .card { position: absolute; box-shadow: 0 12px 30px rgba(0,0,0,.45); overflow: hidden; }

  /* Back side: contact details */
  .card--back {
    left: 390px; top: 65px; width: 750px; height: 380px;
    background: radial-gradient(ellipse 60% 70% at 52% 18%, var(--card-back-light), var(--card-back) 70%);
    text-align: center; color: var(--ink-light);
  }
  .card--back .wordmark {
    position: absolute; left: 300px; top: 100px; width: 190px;
    font-weight: 300; font-size: 58px; letter-spacing: 6px; line-height: 1;
    padding-bottom: 10px; border-bottom: 1.5px solid var(--ink-light);
  }
  .card--back .contact { position: absolute; left: 245px; top: 186px; width: 300px; }
  .card--back .name { font-weight: 300; font-size: 22px; letter-spacing: 1.5px; color: var(--ink-muted); }
  .card--back .email { margin-top: 10px; font-size: 11px; letter-spacing: 1px; color: var(--ink-muted); }
  .card--back .phone { margin-top: 8px; font-size: 11px; letter-spacing: 3.5px; color: var(--ink-muted); }

  /* Front side: brand */
  .card--front { left: 60px; top: 530px; width: 760px; height: 365px; background: var(--card-front); }
  .card--front svg { position: absolute; inset: 0; }
  .card--front .brand { position: absolute; left: 88px; top: 95px; width: 240px; }
  .card--front .brand-name {
    font-weight: 400; font-size: 82px; letter-spacing: 2px; line-height: 1; color: var(--logo-sand);
  }
  .card--front .brand-tag {
    margin: 4px 0 0 100px; font-size: 10px; letter-spacing: 1.5px; color: var(--ink-dim);
  }
</style>
</head>
<body>
<main class="canvas">

  <section class="card card--back" aria-label="Business card, contact side">
    <div class="wordmark">bexil</div>
    <div class="contact">
      <p class="name">TOMAS RELLING</p>
      <p class="email">TOMAS@BEXIL.COM</p>
      <p class="phone">01632 960418</p>
    </div>
  </section>

  <section class="card card--front" aria-label="Business card, brand side">
    <svg width="760" height="365" viewBox="0 0 760 365" aria-hidden="true">
      <defs>
        <linearGradient id="ring" x1="0" y1="0" x2="0" y2="1">
          <stop offset="0" stop-color="var(--ring-blue)"/>
          <stop offset="1" stop-color="var(--ring-blue-deep)"/>
        </linearGradient>
      </defs>
      <circle class="ring" cx="215" cy="120" r="255" fill="url(#ring)"/>
      <circle class="disc" cx="210" cy="115" r="200" fill="var(--disc)"/>
    </svg>
    <div class="brand">
      <p class="brand-name">bexil</p>
      <p class="brand-tag">CONSULTING</p>
    </div>
  </section>

</main>
</body>
</html>
```